Business card design needed

We require business cards for our young and innovative construction team.

Our business is Quarry Ridge Builders and we have used Lime, Navy and white with our colours so far.

We would like business cards that show our passion for perfection and detail, communication and management.

Looking forward to seeing the deigns!!

Communication

Dan Ferrante
Quarry Ridge Builders Pty Ltd
PO Box 617 Birchgrove NSW 2041
Mobile: 0471 362 907
Email: dferrante@quarryridgebuilders.com.au
Web: www.quarryridgebuilders.com.au

```html
<!DOCTYPE html>
<html lang="en">
<head>
<meta charset="utf-8">
<title>Quarry Ridge Builders – Business Card</title>
<link rel="stylesheet" href="https://fonts.googleapis.com/css2?family=Mulish:wght@400;700&display=swap">
<style>
  :root {
    --navy: #3a4a72;
    --navy-deep: #2f3d60;
    --lime: #8dc63f;
    --paper: #fbfbfa;
    --ink: #45526f;
    --backdrop: #e6e8ec;
  }
  html, body {
    margin: 0;
    width: 1200px;
    height: 800px;
    overflow: hidden;
    background: var(--backdrop);
    font-family: "Mulish", Arial, sans-serif;
  }
  .sheet {
    position: relative;
    width: 1200px;
    height: 800px;
    display: flex;
    align-items: center;
    justify-content: center;
    gap: 40px;
  }
  .card {
    position: relative;
    width: 500px;
    height: 286px;
    overflow: hidden;
    box-shadow: 0 6px 18px rgba(30, 40, 70, 0.18);
  }
  /* Front */
  .card--front { background: var(--paper); color: var(--ink); }
  .brand {
    display: flex;
    align-items: center;
    gap: 10px;
    font-weight: 700;
    letter-spacing: 0.04em;
    white-space: nowrap;
  }
  .brand__mark {
    width: 16px;
    height: 16px;
    background: var(--lime);
    flex: none;
  }
  .card--front .brand {
    position: absolute;
    top: 44px;
    right: 34px;
    font-size: 22px;
    color: var(--navy);
  }
  .holder {
    position: absolute;
    left: 34px;
    top: 132px;
    margin: 0;
    font-size: 17px;
    font-weight: 700;
    color: var(--navy);
  }
  .contact {
    position: absolute;
    left: 34px;
    top: 170px;
    margin: 0;
    font-size: 11.5px;
    line-height: 18px;
    color: var(--ink);
    font-style: normal;
  }
  .contact .label { color: var(--lime); font-weight: 700; }
  .rule-lime {
    position: absolute;
    left: 0; right: 0;
    top: 222px;
    height: 4px;
    background: var(--lime);
  }
  .band-navy {
    position: absolute;
    left: 0; right: 0;
    top: 226px;
    bottom: 0;
    background: var(--navy);
  }
  /* Back */
  .card--back {
    background: var(--navy-deep);
    display: flex;
    align-items: center;
    justify-content: center;
  }
  .card--back .brand {
    font-size: 26px;
    color: #ffffff;
  }
</style>
</head>
<body>
<main class="sheet">
  <section class="card card--front" aria-label="Business card front">
    <div class="brand"><span class="brand__mark"></span>Quarry Ridge Builders</div>
    <h1 class="holder">Dan Ferrante</h1>
    <address class="contact">
      PO Box 617 Birchgrove NSW 2041 · <span class="label">M.</span> 0471 362 907<br>
      <span class="label">E.</span> dferrante@quarryridgebuilders.com.au · <span class="label">W.</span> www.quarryridgebuilders.com.au
    </address>
    <div class="rule-lime"></div>
    <div class="band-navy"></div>
  </section>
  <section class="card card--back" aria-label="Business card back">
    <div class="brand"><span class="brand__mark"></span>Quarry Ridge Builders</div>
  </section>
</main>
</body>
</html>
```